Soy Candle Labels

We sell soy candles in recycled wine bottles. The wine bottle is cut in half and filled with pure and natural soy wax and scented with essential oils.
Our product represents good use of up cycling materials for a better use. The product is all natural and eco friendly.
You can see good use of labels and branding for a company in America that does the same thing http://larkmeadow7wicks.example/
Trya dn keep the label uncomplicated like the above labels.
We will need an area to hand stamp the scent. Similar to the labels used on the above website.
We would prefer to use a white or off white paper label with gold or bronze printing - limit the use of colour and keep the label simple and sophisticated.
Emberlace Candle Co. is our company name. Emberlace being the predominant name and candle co. written small underneath right justified.
Die cut labels might look better than a rectangle.
Dimensions should be 90mm Wide x 90mm High
The final design should communicate a professional and quality product. But stay modern and professional. Clean, elegant and sophisticated.
Can use wording such as: Hand Poured, Premium Soy Wax, All Natural, Up cycled
Have a look at the attached image for the look and feel we are going for.
Updates
Designers are having a little bit of trouble interpreting the brief into a viable design. To assist perhaps you can look at WINE LABELS on google images. Design your label around an existing style wine label to give the canld ethe feel of being a bottle of wine. Get creative! :)
Reason: We require more designs. We havnt quite got what were looking for.
Please see brief.

```html
<!DOCTYPE html>
<html lang="en">
<head>
<meta charset="utf-8">
<title>Emberlace Candle Co. — Soy Candle Label</title>
<link rel="stylesheet" href="https://fonts.googleapis.com/css2?family=Signika:wght@500&family=Oswald:wght@300&display=swap">
<style>
  :root {
    --backdrop: #a3864a;
    --paper: #fbfae2;
    --gold: #e8a820;
    --gold-soft: #f1cf72;
    --gold-pale: #f6e6a8;
  }
  * { margin: 0; padding: 0; box-sizing: border-box; }
  html, body {
    width: 1084px;
    height: 1200px;
    overflow: hidden;
    background: var(--backdrop);
  }
  .canvas {
    position: relative;
    width: 1084px;
    height: 1200px;
    background: var(--backdrop);
  }
  .label {
    position: absolute;
    left: 77px;
    top: 98px;
    width: 927px;
    height: 926px;
    background: var(--paper);
    border-radius: 21px;
  }
  .label__frame {
    position: absolute;
    inset: 15px;
    border: 1.5px solid var(--gold);
    border-radius: 14px;
  }
  .claims {
    position: absolute;
    left: 45px;
    top: 42px;
    font-family: "Signika", sans-serif;
    font-weight: 500;
    color: var(--gold);
    line-height: 1;
  }
  .claims__lead { font-size: 41px; margin-bottom: 12px; }
  .claims__line { font-size: 29px; margin-bottom: 10px; }
  .brand {
    position: absolute;
    right: 82px;
    top: 390px;
    text-align: right;
    font-family: "Signika", sans-serif;
    font-weight: 500;
    color: var(--gold);
    line-height: 1;
  }
  .brand__name { font-size: 96px; letter-spacing: 1px; }
  .brand__sub { font-size: 28px; margin-top: 6px; }
  .border-band {
    position: absolute;
    left: 16px;
    right: 16px;
    top: 659px;
    height: 104px;
    background: linear-gradient(180deg, var(--gold-pale), var(--gold-soft) 50%, var(--gold-pale));
  }
  .scent {
    position: absolute;
    left: 44px;
    top: 807px;
    display: flex;
    align-items: center;
    gap: 8px;
  }
  .scent__name {
    font-family: "Oswald", sans-serif;
    font-weight: 300;
    font-size: 44px;
    color: var(--gold);
    line-height: 1;
  }
  .scent__rule {
    width: 2px;
    height: 58px;
    background: var(--gold);
    margin-left: 6px;
  }
  .scent__flourish {
    width: 58px;
    height: 30px;
    border-radius: 15px;
    background: linear-gradient(90deg, var(--gold-soft), var(--gold-pale));
  }
</style>
</head>
<body>
<div class="canvas">
  <section class="label">
    <div class="label__frame"></div>

    <div class="claims">
      <p class="claims__lead">Hand Poured</p>
      <p class="claims__line">All Natural Soy</p>
      <p class="claims__line">12 oz of Premium Soy Wax</p>
    </div>

    <div class="brand">
      <p class="brand__name">Emberlace</p>
      <p class="brand__sub">Candle Co.</p>
    </div>

    <div class="border-band" role="img" aria-label="Gold ornamental scroll border with rosettes running across the label"></div>

    <div class="scent">
      <span class="scent__name">wine bottom</span>
      <span class="scent__rule"></span>
      <span class="scent__flourish" role="img" aria-label="Small gold flourish ornament"></span>
    </div>
  </section>
</div>
</body>
</html>
```